Dental Practice Website design

Design a new website for Brambleford Dental Practice.
Design should be warm, neutral in colour, with some small amount of bright colour if needed but kept to a minimum. Website should look professional, high end. Home page should be easy to navigate and simple for patients to be able to book online.
Logo in files along with some examples of websites that we like. Please ask if any further info needed.
Menu should have:
About
New Patients
Treatments
Fees
Contact Us

Industry/Entity Type

Dentistry

Number of Pages Required

4 page

Font styles to use
Sans Serif

Colors

Designer to choose colors to be used in the design.

Requirements
Must have
• Ravelle ratings badge, book online button,
Nice to have
• neutral, relaxing colours
Should not have
• harsh, bright colours!

```html
<!DOCTYPE html>
<html lang="en">
<head>
<meta charset="utf-8">
<title>Brambleford Dental Practice</title>
<link href="https://fonts.googleapis.com/css2?family=Lexend:wght@400;500;600&family=Lato:wght@300;400;700&display=swap" rel="stylesheet">
<style>
:root{
  --green:#0b6b57;
  --green-dark:#075646;
  --green-soft:#1a6e5c;
  --teal-band:#4f9a8b;
  --mint:#62e0b9;
  --mint-soft:#e3f4ef;
  --ink:#1c2626;
  --muted:#6f7a78;
  --white:#ffffff;
}
*{box-sizing:border-box;margin:0;padding:0}
html,body{width:1200px;height:3266px;overflow:hidden}
body{font-family:"Lato",sans-serif;color:var(--ink);background:var(--white);position:relative}
h1,h2,h3{font-family:"Lexend",sans-serif;font-weight:600;letter-spacing:-0.5px}
.accent{color:var(--green)}
.btn{position:absolute;display:flex;align-items:center;justify-content:center;gap:8px;border-radius:5px;font-size:17px;font-family:"Lato",sans-serif}
.btn-solid{background:var(--green);color:var(--white)}
.btn-outline{border:1.5px solid var(--green);color:var(--green);background:var(--white)}

/* header + hero */
.hero{position:absolute;left:0;top:0;width:1200px;height:600px;background:linear-gradient(180deg,#ffffff 0%,#eef8f5 40%,#dcf1ea 85%,#ffffff 100%)}
.brand{position:absolute;display:flex;align-items:center;gap:14px}
.brand-mark{width:44px;height:44px;border:3px solid var(--green);border-radius:4px}
.brand-name{font-size:18px;line-height:21px;color:#2c3534}
.nav{position:absolute;left:394px;top:46px;display:flex;gap:27px;font-size:15px;color:var(--muted)}
.nav .active{color:var(--green);font-weight:700}
.hero-title{position:absolute;left:110px;top:200px;font-size:62px;line-height:64px;color:var(--ink)}
.hero-text{position:absolute;left:112px;top:354px;width:460px;font-size:20px;line-height:31px;color:var(--muted);font-weight:300}
.portrait-ring{position:absolute;left:670px;top:134px;width:344px;height:344px;border:2px solid var(--green);border-radius:50%}
.portrait{position:absolute;left:695px;top:160px;width:292px;height:292px;border-radius:50%;background:linear-gradient(160deg,#0f7b63,#0a5f4d)}
.badge{position:absolute;width:54px;height:54px;border-radius:50%;background:var(--white);box-shadow:0 4px 14px rgba(0,0,0,.1);display:flex;align-items:center;justify-content:center}
.stats{position:absolute;left:618px;top:433px;width:325px;height:88px;background:var(--white);border-radius:6px;box-shadow:0 6px 20px rgba(0,0,0,.08);display:flex;padding:14px 26px;gap:34px}
.stat-num{font-family:"Lexend",sans-serif;font-weight:600;font-size:30px;color:var(--green);display:flex;align-items:center;gap:8px}
.stat-label{font-size:15px;color:var(--muted);margin-top:2px}

/* about */
.about-photo{position:absolute;left:111px;top:694px;width:454px;height:573px;border-radius:4px;background:linear-gradient(150deg,#d8e6ea,#b9d3de 55%,#8fb4c9)}
.play{position:absolute;left:432px;top:1142px;width:112px;height:112px;border-radius:50%;background:rgba(255,255,255,.8);display:flex;align-items:center;justify-content:center}
.section-title{position:absolute;font-size:42px;color:var(--ink)}
.about-lead{position:absolute;left:617px;top:755px;width:470px;font-size:18px;line-height:34px;color:var(--muted)}
.feature{position:absolute;left:617px;width:470px;display:flex;align-items:center;gap:20px;padding:0 16px;font-size:16.5px;line-height:31px;color:var(--muted)}
.feature.card{background:var(--white);box-shadow:0 6px 22px rgba(0,0,0,.09);border-radius:4px;line-height:26px}
.icon-tile{flex:0 0 58px;height:58px;border-radius:6px;background:var(--mint-soft);display:flex;align-items:center;justify-content:center}

/* team */
.team-glow{position:absolute;left:820px;top:1360px;width:380px;height:300px;border-radius:50%;background:radial-gradient(closest-side,#e7f5f1,rgba(255,255,255,0))}
.team-text{position:absolute;left:111px;top:1497px;width:660px;font-size:18px;line-height:34px;color:var(--muted)}
.team-band{position:absolute;left:0;top:1625px;width:1200px;height:362px;background:var(--teal-band)}
.member{position:absolute;top:1642px;width:295px;height:327px;background:var(--white);border-radius:4px;text-align:center}
.member-photo{margin:17px 17px 0;height:214px;border-radius:3px;background:linear-gradient(180deg,#eef1f4,#dde3e8)}
.member-name{font-family:"Lexend",sans-serif;font-weight:500;font-size:21px;color:var(--green);margin-top:16px}
.member-role{font-size:15px;margin-top:8px;color:var(--ink)}
.dots{position:absolute;left:543px;top:2008px;display:flex;gap:11px}
.dots span{width:9px;height:9px;border-radius:50%;background:#d6dcdb}
.dots span.on{background:var(--green)}

/* join */
.perk{position:absolute;top:2189px;width:135px;height:152px;background:var(--white);box-shadow:0 4px 18px rgba(0,0,0,.09);border-radius:4px;text-align:center;font-size:13.5px;line-height:20px;color:var(--ink);padding-top:20px}
.perk .icon-tile{margin:0 auto 12px;width:62px;height:58px}
.join-text{position:absolute;left:619px;top:2257px;width:460px;font-size:18px;line-height:34px;color:var(--muted)}

/* cta */
.cta{position:absolute;left:0;top:2505px;width:1200px;height:413px;background:var(--green-dark)}
.cta-title{position:absolute;left:0;width:1200px;top:2583px;text-align:center;font-size:43px;color:var(--white)}
.cta-art{position:absolute;left:344px;top:2678px;width:110px;height:68px;border-radius:8px;background:var(--green-soft)}
.cta-sub{position:absolute;left:482px;top:2688px;font-family:"Lexend",sans-serif;font-weight:500;font-size:32px;color:var(--white)}
.mint{color:var(--mint)}

/* footer */
.footer-about{position:absolute;left:111px;top:3080px;width:300px;font-size:14.5px;line-height:26px;color:#4a5453;font-weight:300}
.footer-col{position:absolute;top:3016px}
.footer-col h4{font-family:"Lato",sans-serif;font-weight:700;font-size:17px;color:var(--green);margin-bottom:16px}
.footer-col li{list-style:none;font-size:15px;line-height:26px;color:var(--muted)}
.socials{display:flex;gap:10px}
.socials span{width:17px;height:17px;border-radius:3px;background:var(--green)}
.copyright{position:absolute;left:0;width:1190px;top:3218px;text-align:center;font-size:13.5px;color:var(--muted)}
</style>
</head>
<body>

<section class="hero">
  <div class="brand" style="left:51px;top:34px">
    <div class="brand-mark"></div>
    <div class="brand-name">BRAMBLEFORD<br>Dental practice</div>
  </div>
  <nav class="nav">
    <span class="active">Home</span><span>About</span><span>New Patients</span><span>Treatments</span><span>Fees</span><span>Contact</span>
  </nav>
  <a class="btn btn-outline" style="left:953px;top:34px;width:188px;height:43px">Book Appointment</a>

  <h1 class="hero-title">Your <span class="accent">Smile</span><br><span class="accent">Our</span> Priority</h1>
  <p class="hero-text">Welcome to our friendly dental practice nestled in the heart of beautiful Thornleigh, UK.</p>
  <a class="btn btn-solid" style="left:110px;top:459px;width:140px;height:43px">Book Online</a>
  <a class="btn btn-outline" style="left:274px;top:459px;width:175px;height:43px">View Treatments</a>

  <div class="portrait-ring"></div>
  <div class="portrait" role="img" aria-label="Portrait photo of a smiling patient"></div>
  <div class="badge" style="left:670px;top:180px">
    <svg width="26" height="28" viewBox="0 0 26 28"><path d="M13 5C9 1 2 2 2 9c0 5 3 7 4 17 1 2 3 2 4 0l3-8 3 8c1 2 3 2 4 0 1-10 4-12 4-17 0-7-7-8-11-4z" fill="var(--green)"/></svg>
  </div>
  <div class="badge" style="left:899px;top:124px">
    <svg width="26" height="24" viewBox="0 0 26 24"><path d="M13 23 2 12C-1 8 1 2 7 2c3 0 5 2 6 4 1-2 3-4 6-4 6 0 8 6 5 10z" fill="var(--green)"/></svg>
  </div>
  <div class="badge" style="left:973px;top:346px">
    <svg width="26" height="26" viewBox="0 0 26 26"><rect x="2" y="4" width="22" height="20" rx="2" fill="var(--green)"/><rect x="6" y="1" width="3" height="6" fill="var(--green)"/><rect x="17" y="1" width="3" height="6" fill="var(--green)"/><g fill="#fff"><rect x="6" y="11" width="3" height="3"/><rect x="11.5" y="11" width="3" height="3"/><rect x="17" y="11" width="3" height="3"/><rect x="6" y="17" width="3" height="3"/><rect x="11.5" y="17" width="3" height="3"/><rect x="17" y="17" width="3" height="3"/></g></svg>
  </div>

  <div class="stats">
    <div>
      <div class="stat-num">10k+</div>
      <div class="stat-label">Happy Patients</div>
    </div>
    <div>
      <div class="stat-num">4.7
        <svg width="86" height="15" viewBox="0 0 86 15"><g fill="#f5c518"><polygon points="7.5,0 9.3,5 14.5,5.3 10.4,8.6 11.8,14 7.5,11 3.2,14 4.6,8.6 0.5,5.3 5.7,5"/><polygon transform="translate(17.5 0)" points="7.5,0 9.3,5 14.5,5.3 10.4,8.6 11.8,14 7.5,11 3.2,14 4.6,8.6 0.5,5.3 5.7,5"/><polygon transform="translate(35 0)" points="7.5,0 9.3,5 14.5,5.3 10.4,8.6 11.8,14 7.5,11 3.2,14 4.6,8.6 0.5,5.3 5.7,5"/><polygon transform="translate(52.5 0)" points="7.5,0 9.3,5 14.5,5.3 10.4,8.6 11.8,14 7.5,11 3.2,14 4.6,8.6 0.5,5.3 5.7,5"/><polygon transform="translate(70 0)" points="7.5,0 7.5,11 3.2,14 4.6,8.6 0.5,5.3 5.7,5"/></g></svg>
      </div>
      <div class="stat-label">Ravelle Ratings &nbsp;›</div>
    </div>
  </div>
</section>

<div class="about-photo" role="img" aria-label="Photo of a dentist and assistant with a smiling patient in the chair"></div>
<div class="play"><svg width="44" height="48" viewBox="0 0 44 48"><polygon points="4,2 42,24 4,46" fill="var(--green)"/></svg></div>
<h2 class="section-title" style="left:617px;top:690px">About <span class="accent">Us</span></h2>
<p class="about-lead">Welcome to our friendly dental practice nestled in the heart of beautiful Thornleigh, UK.</p>

<div class="feature card" style="top:834px;height:109px">
  <div class="icon-tile"><svg width="30" height="28" viewBox="0 0 30 28"><path d="M17 13 10 6c-2-3 0-6 3-6 2 0 3 1 4 2 1-1 2-2 4-2 3 0 5 3 3 6z" fill="var(--green)"/><path d="M2 20h6l6 3 10-5c2-1 4 1 2 3l-11 6H2z" fill="var(--green)"/></svg></div>
  <div>At our practice, we believe that a visit to the dentist should be acomfortable and positive experience.</div>
</div>
<div class="feature" style="top:967px;height:94px">
  <div class="icon-tile"><svg width="30" height="26" viewBox="0 0 30 26"><path d="M2 8 9 2l6 3 6-3 7 6-4 6-9 9-9-8z" fill="var(--green)"/></svg></div>
  <div>We create a warm, welcoming atmosphere where patients feel at ease and confident in their dental care.</div>
</div>
<div class="feature" style="top:1084px;height:94px">
  <div class="icon-tile"><svg width="28" height="28" viewBox="0 0 28 28"><path d="M11 6C8 3 2 4 2 10c0 4 2 6 3 14 1 2 3 2 3 0l3-6 3 6c1 2 3 2 3 0 1-8 3-10 3-14 0-6-6-7-9-4z" fill="var(--green)"/><circle cx="22" cy="6" r="5" fill="var(--green)"/></svg></div>
  <div>Our state-of-the-art facilities ensure you receive the latest techniques and treatments for optimal oral health.</div>
</div>
<a class="btn btn-solid" style="left:619px;top:1216px;width:154px;height:43px">Learn More
  <svg width="15" height="15" viewBox="0 0 15 15"><circle cx="7.5" cy="7.5" r="7.5" fill="#fff"/><path d="M5 4l4 3.5L5 11" stroke="var(--green)" stroke-width="2" fill="none"/></svg></a>

<div class="team-glow"></div>
<h2 class="section-title" style="left:110px;top:1430px">Meet our <span class="accent">Team</span></h2>
<p class="team-text">We are delighted to introduce you to our experienced and compassionate dental team. Our team comprises highly skilled dental professionals who are dedicated to providing you with high-quality dental care services.</p>
<a class="btn btn-outline" style="left:940px;top:1505px;width:146px;height:43px">Get in Touch</a>

<div class="team-band"></div>
<div class="member" style="left:112px">
  <div class="member-photo" role="img" aria-label="Photo of the prosthodontist in a white coat"></div>
  <div class="member-name">Marina Holt</div>
  <div class="member-role">Prosthodontist</div>
</div>
<div class="member" style="left:452px">
  <div class="member-photo" role="img" aria-label="Photo of the periodontist holding dental tools"></div>
  <div class="member-name">Julian Ashby</div>
  <div class="member-role">Periodontist</div>
</div>
<div class="member" style="left:793px">
  <div class="member-photo" role="img" aria-label="Photo of the orthodontist in a white coat"></div>
  <div class="member-name">Clara Wendell</div>
  <div class="member-role">Orthodontist</div>
</div>
<div class="dots"><span class="on"></span><span></span><span></span><span></span><span></span><span></span></div>

<div class="perk" style="left:112px">
  <div class="icon-tile"><svg width="30" height="28" viewBox="0 0 30 28"><path d="M17 13 10 6c-2-3 0-6 3-6 2 0 3 1 4 2 1-1 2-2 4-2 3 0 5 3 3 6z" fill="var(--green)"/><path d="M2 20h6l6 3 10-5c2-1 4 1 2 3l-11 6H2z" fill="var(--green)"/></svg></div>
  Complete<br>All- Round Care
</div>
<div class="perk" style="left:267px">
  <div class="icon-tile"><svg width="30" height="30" viewBox="0 0 30 30"><g fill="var(--green)"><circle cx="15" cy="15" r="4"/><circle cx="5" cy="5" r="3"/><circle cx="25" cy="5" r="3"/><circle cx="5" cy="25" r="3"/><circle cx="25" cy="25" r="3"/></g><path d="M5 5 25 25M25 5 5 25" stroke="var(--green)" stroke-width="1.5"/></svg></div>
  Industry Latest<br>Techniques
</div>
<div class="perk" style="left:421px">
  <div class="icon-tile"><svg width="30" height="28" viewBox="0 0 30 28"><circle cx="19" cy="7" r="6" fill="var(--green)"/><path d="M2 18h6l6 3 10-5c2-1 4 1 2 3l-11 6H2z" fill="var(--green)"/></svg></div>
  Quality at<br>Affordable Price
</div>
<a class="btn btn-solid" style="left:261px;top:2377px;width:146px;height:43px">Join Practice</a>
<h2 class="section-title" style="left:618px;top:2182px">Join Our <span class="accent">Practice</span></h2>
<p class="join-text">If you're looking for an exceptional dental practice, we're here to help! Our team is made up of highly skilled professionals who are dedicated to ensuring that all our patients receive top-notch care in a welcoming and comfortable environment.</p>

<section class="cta"></section>
<h2 class="cta-title">Book an <span class="mint">Appointment</span> Now</h2>
<div class="cta-art" role="img" aria-label="Line illustration of a bright smile with sparkles"></div>
<div class="cta-sub">Your <span class="mint">Smile</span> Matters to Us</div>
<a class="btn" style="left:476px;top:2789px;width:246px;height:41px;background:#fff;color:var(--green-dark)">Book an Appointment Now</a>

<footer>
  <div class="brand" style="left:112px;top:3028px">
    <div class="brand-mark"></div>
    <div class="brand-name">BRAMBLEFORD<br>Dental practice</div>
  </div>
  <p class="footer-about">We are passionate about improving dental health and helping you achieve your brightest smile and are honoured that you're considering us for your dental needs.</p>
  <div class="footer-col" style="left:555px">
    <h4>Explore</h4>
    <ul><li>Home</li><li>About Us</li><li>New Patients</li><li>Treatments</li><li>Fees</li></ul>
  </div>
  <div class="footer-col" style="left:770px">
    <h4>Useful links</h4>
    <ul><li>Privacy</li><li>Terms of Service</li><li>Support</li><li>Licenses</li><li>Cookies</li></ul>
  </div>
  <div class="footer-col" style="left:983px">
    <h4>Follow us</h4>
    <div class="socials"><span></span><span></span><span></span><span></span></div>
  </div>
  <p class="copyright">© Copyright 2025 Brambleford Dental Practice All rights reserved.</p>
</footer>

</body>
</html>
```